Veltrano.co - Polar Expeditions Specialists

We need a modern, visually striking business card for Veltrano.co, a company specialized in selling expedition cruises to the most remote regions on Earth, with a focus on the Arctic and Antarctica. The design should instantly communicate that the cardholder is an expert in polar travel. Use clean, premium aesthetics with cool tones like icy blue and white, possibly incorporating polar imagery (ice, glaciers, penguins, etc.)

Attached the logo

Contact Information for Business Card

Feels high-end and trustworthy.. Visually memorable — encourages people to keep it

Colors
0054AA
0677BA
7BADD7
CADEEF
E8F1F8

Requirements
Must have
• ice, glaciers, penguins, montains
Nice to have
• modern, transparente,

```html
<!DOCTYPE html>
<html lang="en">
<head>
<meta charset="utf-8">
<title>Veltrano.co – Business Card</title>
<link rel="stylesheet" href="https://fonts.googleapis.com/css2?family=Montserrat:wght@300;400;700&family=Poppins:wght@600;700&display=swap">
<style>
  :root {
    --page-bg: #ececec;
    --card-white: #ffffff;
    --brand-blue: #2c6fb5;
    --rule-blue: #3a7cc0;
    --ink: #3a3a3a;
    --back-top: #5e97cc;
    --back-bottom: #4a84c0;
    --back-ice: #7badd7;
  }
  * { box-sizing: border-box; margin: 0; padding: 0; }
  html, body { width: 1192px; height: 1200px; overflow: hidden; }
  body { background: var(--page-bg); position: relative; font-family: "Montserrat", sans-serif; }

  .card {
    position: absolute;
    left: 219px;
    width: 754px;
    height: 433px;
    border-radius: 32px;
    overflow: hidden;
    box-shadow: 0 10px 24px rgba(0,0,0,0.16);
  }
  .card--front { top: 145px; background: var(--card-white); }
  .card--back { top: 622px; }

  .brand { position: absolute; display: flex; align-items: center; }
  .brand__dot { border-radius: 50%; flex-shrink: 0; }
  .brand__text { display: flex; flex-direction: column; }
  .brand__name { font-family: "Poppins", sans-serif; font-weight: 700; line-height: 1; letter-spacing: -0.5px; }
  .brand__tagline { font-family: "Poppins", sans-serif; font-weight: 600; line-height: 1.2; }

  .card--front .brand { right: 40px; top: 52px; gap: 22px; }
  .card--front .brand__dot { width: 50px; height: 50px; background: var(--brand-blue); }
  .card--front .brand__name { font-size: 43px; color: var(--brand-blue); }
  .card--front .brand__tagline { font-size: 13.5px; color: var(--brand-blue); margin-top: 6px; }

  .holder { position: absolute; left: 40px; top: 195px; }
  .holder__name { font-weight: 700; font-size: 28px; color: var(--brand-blue); letter-spacing: 0.5px; line-height: 1.05; }
  .holder__role { font-weight: 400; font-size: 19px; color: var(--ink); line-height: 1.2; }

  .divider { position: absolute; left: 40px; right: 40px; top: 277px; height: 1.5px; background: var(--rule-blue); }

  .contacts { position: absolute; left: 40px; top: 306px; list-style: none; }
  .contacts li { display: flex; align-items: center; gap: 8px; font-size: 18px; color: var(--ink); height: 31px; }
  .contacts svg { width: 13px; height: 13px; fill: var(--brand-blue); }

  .address { position: absolute; right: 40px; top: 342px; text-align: right; font-size: 18px; color: var(--ink); line-height: 25px; font-style: normal; }

  .back-photo {
    position: absolute; inset: 0;
    background:
      radial-gradient(ellipse 45% 55% at 48% 50%, rgba(123,173,215,0.45), transparent 70%),
      linear-gradient(180deg, var(--back-top), var(--back-bottom));
  }
  .card--back .brand { left: 132px; top: 160px; gap: 24px; }
  .card--back .brand__dot { width: 112px; height: 112px; background: var(--card-white); }
  .card--back .brand__name { font-size: 60px; color: var(--card-white); }
  .card--back .brand__tagline { font-size: 19.5px; color: var(--card-white); margin-top: 8px; }
</style>
</head>
<body>
  <section class="card card--front">
    <div class="brand">
      <span class="brand__dot"></span>
      <div class="brand__text">
        <span class="brand__name">Veltrano.co</span>
        <span class="brand__tagline">Polar Expeditions Specialists</span>
      </div>
    </div>

    <div class="holder">
      <h1 class="holder__name">NORA LINDQVIST</h1>
      <p class="holder__role">CEO / Founder</p>
    </div>

    <div class="divider"></div>

    <ul class="contacts">
      <li>
        <svg viewBox="0 0 16 16" aria-hidden="true"><path d="M1 6c0-2 3-3 7-3s7 1 7 3v1h-3V5.5C11 5 9.5 5 8 5s-3 0-4 .5V7H1zM4 8h8l2 6H2z"/></svg>
        +43 664 20 87 315
      </li>
      <li>
        <svg viewBox="0 0 16 16" aria-hidden="true"><path d="M1 6l7-5 7 5v9H1zM2.5 6.5L8 10l5.5-3.5L8 3z"/></svg>
        nora.lindqvist@veltrano.co
      </li>
      <li>
        <svg viewBox="0 0 16 16" aria-hidden="true"><path d="M8 1a7 7 0 1 0 0 14A7 7 0 0 0 8 1zm-1 2.5c1 .5 1 1.5 0 2.5s-2 .5-2 2 2 1 2 3-1 2-2 1.5A5.5 5.5 0 0 1 7 3.5zm3 2c1 0 2 1 1.5 2.5S10 9 10 10s-1 2-1.5 1.5 0-2-.5-3 0-3 2-3z"/></svg>
        www.veltrano.co
      </li>
    </ul>

    <address class="address">
      P.O. Box 3160 Harbour Lane<br>
      Northland AV 4718
    </address>
  </section>

  <section class="card card--back">
    <div class="back-photo" role="img" aria-label="Photo of a polar bear walking on snow, tinted icy blue"></div>
    <div class="brand">
      <span class="brand__dot"></span>
      <div class="brand__text">
        <span class="brand__name">Veltrano.co</span>
        <span class="brand__tagline">Polar Expeditions Specialists</span>
      </div>
    </div>
  </section>
</body>
</html>
```